Torvane Email Signature Banners – Fabrication Capability Series

www.Torvane.com.au is an Australian engineering and fabrication company specialising in fabrication and welding of :
steel piping spools,
skids and frames,
small volume process steel tanks
and general steel fabrication
We require four distinct banner designs for use in Microsoft Lintaro email signatures. Each banner will highlight a specific capability while maintaining a consistent brand identity.
Deliverables
Four banners total:
Piping Spools Fabrication – focus on precision welding and stainless steel pipework
Skid & Frames Fabrication – highlight skid systems and structural frames
Small Steel Tanks Fabrication – show fabricated tanks and workshop craftsmanship
General Fabrication Solutions – broad steel fabrication theme for company-wide use
Dimensions: 600–700 px wide × 100 px high
Format: PNG (preferred), small file size prefered
Resolution: 72 dpi
Background: non-transparent, industrial or workshop setting
Text examples:
1. Piping Spools Fabrication
Option A: “Expert Fabrication Solutions for Process Piping”
Option B: “Precision Welding for Complex Systems”
Option C: “Delivering Quality in Every Spool”
Option D: “Engineered for Flow, Built for Strength”
2. Skid & Frames Fabrication
Option A: “Custom Engineered Modular Systems”
Option B: “Built Strong. Designed Smart.”
Option C: “Reliable Frames for Industrial Performance”
Option D: “Modular Fabrication for Seamless Integration”
3. Small Steel Tanks Fabrication
Option A: “Precision Built for Your Needs”
Option B: “Compact Strength. Proven Durability.”
Option C: “Fabricated for Performance and Longevity”
Option D: “Small Tanks. Big Reliability.”
4. General Fabrication Solutions
Option A: “Quality Craftsmanship, Proven Results”
Option B: “Your Partner in Precision Fabrication”
Option C: “Engineering Excellence in Every Weld”
Option D: “Australian Fabrication. Global Standards.”
Style Direction
Clean, professional, and engineering‑focused
Use Torvane brand colours
Blend photo realism with vector clarity (no heavy gradients)
Include subtle industrial textures or workshop imagery
Typography: bold sans‑serif, legible at small scale
Usage Context
These banners will appear at the bottom of staff email signatures via Lintaro Email Signature Tool for Microsoft 365, so clarity and fast loading are essential. No Logo is required in the banners.
Reference
Existing Torvane signature is attached. Colour palette to match the signature style and logo.
Target Market(s)
Engineering and construction companies,
Industry/Entity Type
Engineering fabrication design
Look and feel

```html
<!DOCTYPE html>
<html lang="en">
<head>
<meta charset="UTF-8">
<title>Torvane Email Signature Banners</title>
<link rel="stylesheet" href="https://fonts.googleapis.com/css2?family=Poppins:wght@500;600;700&display=swap">
<style>
  :root {
    --stage-grey: #7b7b7b;
    --steel-dark: #141414;
    --steel-mid: #3a3a3c;
    --steel-light: #6e6a66;
    --brand-blue: #1a93c9;
    --sky-blue: #2aace3;
    --title-blue: #1e9ad5;
    --ink: #1d1d1d;
    --white: #ffffff;
  }
  * { margin: 0; padding: 0; box-sizing: border-box; }
  html, body {
    width: 1200px;
    height: 462px;
    overflow: hidden;
    background: var(--stage-grey);
    font-family: "Poppins", sans-serif;
  }
  .canvas {
    position: relative;
    width: 1200px;
    height: 462px;
    background: var(--stage-grey);
  }
  .banner {
    position: absolute;
    left: 78px;
    width: 1049px;
    height: 149px;
    overflow: hidden;
  }
  .banner--spools { top: 52px; }
  .banner--skids { top: 255px; background: var(--sky-blue); }

  .welding-photo {
    position: absolute;
    inset: 0;
    background: linear-gradient(100deg, var(--steel-dark) 0%, var(--steel-mid) 22%, var(--steel-light) 40%, #2b2b2b 62%, var(--steel-dark) 78%);
  }
  .brand-panel {
    position: absolute;
    inset: 0;
    width: 100%;
    height: 100%;
  }
  .spools-title {
    position: absolute;
    left: 51px;
    top: 93px;
    color: var(--white);
    font-weight: 600;
    font-size: 33px;
    line-height: 1;
    letter-spacing: 0.2px;
    white-space: nowrap;
  }
  .spools-tagline {
    position: absolute;
    right: 49px;
    top: 28px;
    width: 260px;
    color: var(--white);
    font-weight: 600;
    font-size: 20px;
    line-height: 35px;
    text-align: right;
  }

  .blueprint-art {
    position: absolute;
    inset: 0;
    background: linear-gradient(90deg, #27a7df 0%, #31b2e8 50%, #27a7df 100%);
  }
  .title-card {
    position: absolute;
    left: 273px;
    top: 35px;
    width: 504px;
    height: 78px;
    background: var(--white);
    text-align: center;
  }
  .skids-title {
    margin-top: 4px;
    color: var(--title-blue);
    font-weight: 600;
    font-size: 32px;
    line-height: 42px;
    white-space: nowrap;
  }
  .skids-tagline {
    color: var(--ink);
    font-weight: 600;
    font-size: 15px;
    line-height: 24px;
    white-space: nowrap;
  }
</style>
</head>
<body>
<main class="canvas">

  <section class="banner banner--spools" aria-label="Piping Spools Fabrication banner">
    <div class="welding-photo" role="img" aria-label="Photo of a gloved welder welding a stainless steel pipe spool"></div>
    <svg class="brand-panel" viewBox="0 0 1049 149" preserveAspectRatio="none" aria-hidden="true">
      <polygon points="755,0 765,0 705,149 695,149" fill="var(--brand-blue)"/>
      <polygon points="777,0 1049,0 1049,149 717,149" fill="var(--brand-blue)"/>
    </svg>
    <h2 class="spools-title">Piping Spools Fabrication</h2>
    <p class="spools-tagline">Expert Fabrication Solutions for Process Piping</p>
  </section>

  <section class="banner banner--skids" aria-label="Skid and Frames Fabrication banner">
    <div class="blueprint-art" role="img" aria-label="White line drawing of a modular process skid with pipework and structural frames"></div>
    <div class="title-card">
      <h2 class="skids-title">Skid &amp; Frames Fabrication</h2>
      <p class="skids-tagline">Custom Engineered Modular Systems</p>
    </div>
  </section>

</main>
</body>
</html>
```